Book cover for book about Climate Change

Looking for a clean, bold, and attractive cover for a mass-market paperback (5.5"x 8.5") about solving the climate change problem. Title is either "Where the Rivers Meet” or A Harbor Made of Glass” (your choice), subtitle is "A practical field guide to mending the weather — so that the young ones after us inherit steady seasons and open skies," author is Lorne Whitcombe. Thinking that it *might* feature an image of Earth (or a portion thereof) and its very thin layer of atmosphere -- but STRONGLY encourage other ideas too!

Requirements
Nice to have
• Keep it positive — NOT scary doom-and-gloom

```html
<!DOCTYPE html>
<html lang="en">
<head>
<meta charset="utf-8">
<title>A Harbor Made of Glass — Lorne Whitcombe</title>
<link rel="stylesheet" href="https://fonts.googleapis.com/css2?family=Cinzel:wght@400;500&family=Playfair+Display:wght@400;900&family=Lora:ital@1&display=swap">
<style>
  :root {
    --page: #ffffff;
    --sky-pale: #eef5fb;
    --sky-mid: #a9cdeb;
    --sky-deep: #5fa3d9;
    --art-top: #cfe2f2;
    --art-mid: #8db9df;
    --art-low: #a7c6c9;
    --ink: #121417;
    --orange: #f28a1f;
    --rule: #1d2a36;
  }
  * { box-sizing: border-box; margin: 0; padding: 0; }
  html, body {
    width: 1200px; height: 691px; overflow: hidden;
    background: var(--page);
  }
  .cover {
    position: absolute; left: 376px; top: 0;
    width: 447px; height: 691px; overflow: hidden;
    background:
      radial-gradient(ellipse 75% 45% at 50% 50%, rgba(255,255,255,0.55), rgba(255,255,255,0) 70%),
      linear-gradient(180deg, var(--sky-pale) 0%, var(--sky-mid) 28%, var(--sky-deep) 52%, var(--sky-mid) 78%, var(--sky-pale) 100%);
    text-align: center; color: var(--ink);
  }
  .title-top {
    position: absolute; top: 28px; left: 0; right: 0;
    font-family: "Playfair Display", serif; font-weight: 400;
    font-size: 96px; line-height: 1; letter-spacing: 2px;
  }
  .title-main {
    position: absolute; top: 108px; left: 0; right: 0;
    font-family: "Playfair Display", serif; font-weight: 900;
    font-size: 86px; line-height: 1; color: var(--orange); letter-spacing: 1px;
  }
  .title-tail {
    position: absolute; top: 192px; left: 0; right: 0;
    display: flex; align-items: center; justify-content: center; gap: 10px;
    font-family: "Playfair Display", serif; font-weight: 400;
    font-size: 31px; line-height: 1; letter-spacing: 1px;
  }
  .title-tail::before, .title-tail::after {
    content: ""; width: 28px; height: 2px; background: var(--ink);
  }
  .cover-art {
    position: absolute; left: 40px; top: 246px; width: 367px; height: 234px;
    border-radius: 6px;
    background: linear-gradient(180deg, var(--art-top) 0%, var(--art-mid) 55%, var(--art-low) 100%);
    opacity: 0.75;
  }
  .rule {
    position: absolute; left: 65px; width: 317px; height: 1px; background: var(--rule);
  }
  .rule-top { top: 496px; }
  .rule-bottom { top: 601px; }
  .subtitle {
    position: absolute; top: 505px; left: 0; right: 0;
    font-family: "Cinzel", serif; font-weight: 400;
    font-size: 21px; line-height: 23px; letter-spacing: 0.5px;
  }
  .tagline {
    position: absolute; top: 555px; left: 0; right: 0;
    font-family: "Lora", serif; font-style: italic;
    font-size: 16px; line-height: 19px;
  }
  .author {
    position: absolute; top: 628px; left: 0; right: 0;
    font-family: "Cinzel", serif; font-weight: 500;
    font-size: 33px; line-height: 1; color: var(--orange); letter-spacing: 2px;
  }
</style>
</head>
<body>
  <main class="cover">
    <h1>
      <span class="title-top">A</span>
      <span class="title-main">HARBOR</span>
      <span class="title-tail">MADE OF GLASS</span>
    </h1>
    <div class="cover-art" role="img" aria-label="Photograph of an open hand holding a small Earth globe topped with trees"></div>
    <div class="rule rule-top"></div>
    <p class="subtitle">A PRACTICAL FIELD GUIDE<br>TO MENDING THE WEATHER</p>
    <p class="tagline">– so that the young ones after us inherit<br>steady seasons and open skies</p>
    <div class="rule rule-bottom"></div>
    <p class="author">LORNE WHITCOMBE</p>
  </main>
</body>
</html>
```